Letter design, envelope design, and more

Hello, we the Tavrin Gmbh are looking for our shop. Letter C5. Design does not have to be like a business card, so it can have straight lines. Only the color is important. The logo is the text under TaVRin omit.It should not be playful but Profesionel

Font styles to use
Sans Serif

Colors
0555a3
3176b5
85abd2
85cae6
34a7d8
0792cd
cee9f5
cfdfed
000000

Requirements
Must have
• Color like business card, Please, with the text under TaVRin, Correct address Lindmattstr. 4 Zip code 9517 Seewil, as well as Couvert Without addressing only design and logo with TaVrn
Nice to have
• more writing articles
Should not have
• Not too colored, Text under TaVRin, bright colors

```html
<!DOCTYPE html>
<html lang="en">
<head>
<meta charset="utf-8">
<title>Tavrin Gmbh – Letterhead</title>
<link rel="stylesheet" href="https://fonts.googleapis.com/css2?family=Source+Sans+3:wght@400;500;600;700&display=swap">
<style>
  :root {
    --stage: #404040;
    --frame: #ffffff;
    --paper: #ffffff;
    --navy: #03196b;
    --sky: #a9c6d8;
    --ink: #000000;
  }
  * { box-sizing: border-box; margin: 0; padding: 0; }
  html, body { width: 1200px; height: 1006px; overflow: hidden; background: var(--frame); }
  body { position: relative; font-family: "Source Sans 3", sans-serif; color: var(--ink); }

  .stage { position: absolute; left: 19px; top: 17px; width: 1162px; height: 970px; background: var(--stage); }

  .letter { position: absolute; left: 320px; top: 78px; width: 578px; height: 817px; background: var(--paper); overflow: hidden; box-shadow: -8px 8px 10px rgba(0,0,0,0.35); }
  .letter__band { position: absolute; left: 0; top: 0; width: 100%; height: 27px; background: var(--navy); }

  .brand { position: absolute; left: 34px; top: 52px; display: flex; align-items: center; gap: 8px; }
  .brand__mark { width: 30px; height: 30px; background: var(--navy); }
  .brand__name { font-size: 34px; font-weight: 700; color: var(--navy); letter-spacing: 0.5px; line-height: 1; }

  .letter__body { position: absolute; left: 85px; top: 229px; width: 408px; font-size: 11.6px; line-height: 12.6px; }
  .letter__salutation { margin-bottom: 40px; }
  .letter__body p + p { margin-top: 12.6px; }

  .signature { position: absolute; left: 85px; top: 528px; width: 92px; height: 44px; background: linear-gradient(90deg, #f2f2f2, #e6e6e6); }
  .signer { position: absolute; left: 85px; top: 591px; font-size: 12px; line-height: 17.5px; }

  .footer__block { position: absolute; left: 0; top: 737px; width: 149px; height: 62px; background: var(--sky); }
  .contact { position: absolute; top: 746px; display: flex; flex-direction: column; align-items: center; transform: translateX(-50%); }
  .contact svg { width: 24px; height: 24px; }
  .contact__label { margin-top: 5px; font-size: 9.4px; font-weight: 500; white-space: nowrap; }
  .contact__label .sep { display: inline-block; width: 1px; height: 14px; background: var(--ink); margin: 0 3px -3px; }
</style>
</head>
<body>
  <div class="stage"></div>

  <article class="letter">
    <div class="letter__band"></div>

    <div class="brand">
      <span class="brand__mark"></span>
      <span class="brand__name">TaVRin</span>
    </div>

    <section class="letter__body">
      <p class="letter__salutation">Dear Mr. Berger,</p>
      <p>Lorem ipsum dolor sit amet, consectetur adipiscing elit. Cras elementum eget sem quis tincidunt. Suspendisse congue accumsan ipsum ac auctor.</p>
      <p>Fusce sagittis tellus a urna ornare eleifend. Interdum et malesuada fames ac ante ipsum primis in faucibu. Fusce pulvinar sodales diam et consequat. Praesent placerat nulla vitae nisl ullamcorper, vel facilisis lorem consequat. Fusce sagittis tellus a urna ornare eleifend. Interdum et malesuada fames ac ante ipsum primis in faucibu. Fusce pulvinar sodales diam et consequat. Praesent placerat nulla vitae nisl ullamcorper, vel facilisis lorem consequat.</p>
      <p>Fusce sagittis tellus a urna ornare eleifend. Interdum et malesuada fames ac ante ipsum primis in faucibu. Fusce pulvinar sodales diam et consequat. Praesent placerat nulla vitae nisl ullamcorper, vel facilisis lorem consequat.</p>
      <p>Lorem ipsum dolor sit amet, consectetur adipiscing elit. Cras elementum eget sem quis tincidunt.</p>
    </section>

    <div class="signature" role="img" aria-label="Handwritten signature of the sender"></div>
    <div class="signer">
      <p>Lukas Berger</p>
      <p>Co Founder &amp; CEO</p>
    </div>

    <div class="footer__block"></div>

    <div class="contact" style="left:209px">
      <svg viewBox="0 0 24 24" fill="none" stroke="#000" stroke-width="1"><circle cx="12" cy="12" r="11.2"/><circle cx="12" cy="12" r="6.5"/><ellipse cx="12" cy="12" rx="2.8" ry="6.5"/><path d="M5.5 12h13M6.5 8.8h11M6.5 15.2h11"/></svg>
      <span class="contact__label">www.tavrin.ch</span>
    </div>
    <div class="contact" style="left:302px">
      <svg viewBox="0 0 24 24" fill="none" stroke="#000" stroke-width="1"><circle cx="12" cy="12" r="11.2"/><path d="M8.3 6.5l2 2.3-1.2 1.6c.9 1.8 2.2 3.1 4 4l1.6-1.2 2.3 2-1.3 1.8c-3.8-.4-7.4-4-7.8-7.8z"/></svg>
      <span class="contact__label">+41 71 555 02 48</span>
    </div>
    <div class="contact" style="left:397px">
      <svg viewBox="0 0 24 24" fill="none" stroke="#000" stroke-width="1"><circle cx="12" cy="12" r="11.2"/><path d="M6.5 12l11-4.5-3.5 10-2.5-3.5zM11.5 14l6-6.5"/></svg>
      <span class="contact__label">info@tavrin.ch</span>
    </div>
    <div class="contact" style="left:511px">
      <svg viewBox="0 0 24 24" fill="none" stroke="#000" stroke-width="1"><circle cx="12" cy="12" r="11.2"/><path d="M12 18.5s-4.2-4.6-4.2-7.6a4.2 4.2 0 018.4 0c0 3-4.2 7.6-4.2 7.6z"/><circle cx="12" cy="10.8" r="1.5"/></svg>
      <span class="contact__label">Lindmattstr. 4<span class="sep"></span>9517 Seewil</span>
    </div>
  </article>
</body>
</html>
```